Income Tax Flyer - Updates Needed

Just need to update this flyer design and give it a new look. We would like to keep all the same wording but make it stand out a little more. Our selling point is the "Same Day Tax Advance up to $6,000"

Lending, Small Loans, Tax Services, Title Loans, Personal Loans

```html
<!DOCTYPE html>
<html lang="en">
<head>
<meta charset="utf-8">
<title>Same Day Tax Advance Flyer</title>
<link href="https://fonts.googleapis.com/css2?family=Lora:wght@400;600;700&display=swap" rel="stylesheet">
<style>
  :root {
    --green: #0f5130;
    --green-deep: #0a3b23;
    --red: #c11f28;
    --gold: #f6c64f;
    --charcoal: #262626;
    --mint: #e3efe9;
    --white: #ffffff;
    --ink: #222222;
  }
  * { margin: 0; padding: 0; box-sizing: border-box; }
  html, body { width: 848px; height: 1200px; overflow: hidden; background: var(--white); }
  .flyer {
    position: relative; width: 848px; height: 1200px; overflow: hidden;
    font-family: "Lora", Georgia, serif; background: var(--white); color: var(--ink);
  }

  .top-bar {
    position: absolute; left: 0; top: 0; width: 848px; height: 72px;
    background: var(--green); display: flex; align-items: center; padding-left: 40px;
  }
  .brand { display: flex; align-items: center; gap: 12px; color: var(--white); font-weight: 700; font-size: 28px; }
  .brand-dot { width: 16px; height: 16px; border-radius: 50%; background: var(--white); flex: none; }

  .hero-photo {
    position: absolute; left: 0; top: 72px; width: 848px; height: 398px;
    background:
      radial-gradient(ellipse at 45% 35%, #f1e9e1 0%, rgba(241,233,225,0) 45%),
      linear-gradient(180deg, #e9e6e0 0%, #d8d2cb 55%, #8a7a70 85%, #7b6c63 100%);
  }

  .offer-card {
    position: absolute; left: 40px; top: 392px; width: 768px; height: 222px;
    background: var(--red); border-radius: 18px; border: 5px solid var(--white);
    box-shadow: 0 14px 30px rgba(0,0,0,0.28);
    display: flex; flex-direction: column; align-items: center; justify-content: center;
    color: var(--white); text-align: center;
  }
  .offer-lead { font-size: 46px; font-weight: 700; line-height: 1.1; letter-spacing: 0.5px; }
  .offer-rule { width: 120px; height: 4px; background: var(--gold); border-radius: 2px; margin: 10px 0 4px; }
  .offer-amount { font-weight: 700; line-height: 1.05; }
  .offer-upto { font-size: 40px; font-weight: 600; }
  .offer-figure { font-size: 92px; color: var(--gold); }

  .apply { position: absolute; left: 0; top: 632px; width: 848px; text-align: center; font-weight: 700; color: var(--green); }
  .apply-lead { font-size: 32px; letter-spacing: 4px; line-height: 40px; }
  .apply-range { font-size: 54px; line-height: 68px; }
  .apply-range .amount { color: var(--red); }

  .file-bar {
    position: absolute; left: 0; top: 756px; width: 848px; height: 72px;
    background: var(--charcoal); color: var(--white);
    display: flex; align-items: center; justify-content: center; font-size: 30px;
  }

  .features {
    position: absolute; left: 0; top: 828px; width: 848px; height: 130px;
    background: var(--mint); display: flex; align-items: center; justify-content: center; gap: 16px;
  }
  .feature {
    width: 250px; height: 92px; background: var(--white); border-radius: 12px;
    border-bottom: 4px solid var(--green);
    display: flex; align-items: center; gap: 14px; padding: 0 14px;
    font-size: 19px; line-height: 1.35; color: var(--ink);
  }
  .feature-icon { width: 48px; height: 48px; border-radius: 50%; background: var(--green); flex: none; display: flex; align-items: center; justify-content: center; }

  .contact-bar {
    position: absolute; left: 0; top: 958px; width: 848px; height: 84px;
    background: var(--red); color: var(--white);
    display: flex; align-items: center; justify-content: center; gap: 20px;
  }
  .contact-label { font-size: 28px; margin-right: 14px; }
  .contact-phone { font-size: 40px; font-weight: 600; letter-spacing: 0.5px; }

  .addresses {
    position: absolute; left: 0; top: 1062px; width: 848px; text-align: center;
    font-style: normal; font-size: 22px; line-height: 36px; color: var(--ink);
  }
</style>
</head>
<body>
<main class="flyer">
  <header class="top-bar">
    <div class="brand"><span class="brand-dot"></span><span>Harbor Ledger Financial Group</span></div>
  </header>

  <div class="hero-photo" role="img" aria-label="Smiling woman on a sofa at home celebrating while reading a tax document next to a laptop"></div>

  <section class="offer-card">
    <h1 class="offer-lead">Same Day Tax Advance</h1>
    <span class="offer-rule"></span>
    <p class="offer-amount"><span class="offer-upto">up to</span> <span class="offer-figure">$6,000</span></p>
  </section>

  <section class="apply">
    <h2 class="apply-lead">APPLY HERE FOR</h2>
    <p class="apply-range"><span class="amount">$5,000 - $6,000</span> TODAY!</p>
  </section>

  <div class="file-bar">File your taxes and apply for an Easy Advance!</div>

  <section class="features">
    <div class="feature">
      <span class="feature-icon">
        <svg width="30" height="30" viewBox="0 0 34 34" fill="none" stroke="#fff" stroke-width="2.6" stroke-linecap="round">
          <path d="M29 17a12 12 0 1 1-4-9"/><path d="M26 3v6h-6"/><path d="M17 9v8l-5 4"/>
        </svg>
      </span>
      <span>Available in<br>24 Hours or Less</span>
    </div>
    <div class="feature">
      <span class="feature-icon">
        <svg width="30" height="30" viewBox="0 0 34 34" fill="none" stroke="#fff" stroke-width="2.4" stroke-linecap="round">
          <rect x="9" y="5" width="18" height="24" rx="2"/><path d="M14 12h9M14 17h9M14 22h6"/>
          <circle cx="8" cy="10" r="5" fill="#0f5130"/><path d="M5.5 10l2 2 3-3.5"/>
        </svg>
      </span>
      <span>Choose Your<br>Loan Amount</span>
    </div>
    <div class="feature">
      <span class="feature-icon">
        <svg width="30" height="30" viewBox="0 0 34 34" fill="none" stroke="#fff" stroke-width="2.4" stroke-linecap="round">
          <circle cx="18" cy="13" r="7"/><path d="M18 9v8M20 10.5h-3a1.5 1.5 0 0 0 0 3h2a1.5 1.5 0 0 1 0 3h-3"/>
          <path d="M4 24h4l6 3h9l6-4"/><path d="M4 21v8"/>
        </svg>
      </span>
      <span>Quick and<br>Easy</span>
    </div>
  </section>

  <section class="contact-bar">
    <span class="contact-label">Contact us Today!</span>
    <svg width="44" height="44" viewBox="0 0 44 44" fill="none" stroke="#fff" stroke-width="2.4" aria-hidden="true">
      <circle cx="22" cy="22" r="20"/>
      <path d="M15 12l4 0 2 6-3 2c1.5 3 3.5 5 6 6l2-3 6 2v4c-9 1-18-8-17-17z" stroke-linejoin="round"/>
    </svg>
    <span class="contact-phone">+1 800 555 0142</span>
  </section>

  <address class="addresses">
    118 Birchwood Court, Topeka, KS 66612<br>
    4820 Alder Lane, Salt Lake City, UT 84104<br>
    307 Marlow Lane, Tuckahoe, NY 10707
  </address>
</main>
</body>
</html>
```